Talvenor Capital LLC

Need Professional Business cards for New Investment Fund

Target Market(s)

High Quality investors

Industry/Entity Type

Financial

Contact Information for Business Card

Phone Number +1 555 284 6190
Name Lukas Varenko
Title Fund Manager
email lv@FundTalvenor.com
Website www.FundTalvenor.com

Colors

Designer to choose colors to be used in the design.

Requirements
Must have
• Must have our Logo and all of the above. Must be made so lettering and loge can be raised

```html
<!DOCTYPE html>
<html lang="en">
<head>
<meta charset="utf-8">
<title>Talvenor Capital LLC – Business Card</title>
<link rel="stylesheet" href="https://fonts.googleapis.com/css2?family=Montserrat:wght@400;600;700&display=swap">
<style>
  :root {
    --backdrop: #d8d8d8;
    --card-light: #efefef;
    --card-dark: #2a2a2a;
    --ink-dark: #3f4a40;
    --ink-body: #2a2a2a;
    --accent-green: #1fe01f;
    --white: #ffffff;
  }
  * { margin: 0; padding: 0; box-sizing: border-box; }
  html, body {
    width: 1200px; height: 965px; overflow: hidden;
    background: var(--backdrop);
    font-family: "Montserrat", sans-serif;
  }
  .canvas { position: relative; width: 1200px; height: 965px; }
  .card {
    position: absolute; top: 159px; width: 383px; height: 669px;
  }
  .card--front { left: 186px; background: var(--card-light); }
  .card--back {
    left: 653px;
    background: linear-gradient(160deg, #3a3a3a 0%, #2a2a2a 50%, #1e1e1e 100%);
  }
  .brand {
    position: absolute; left: 0; right: 0; top: 180px;
    display: flex; align-items: center; justify-content: center; gap: 12px;
  }
  .brand__square { width: 26px; height: 26px; background: var(--accent-green); flex: none; }
  .brand__name {
    font-weight: 700; font-size: 40px; letter-spacing: 1px;
    color: var(--ink-dark); line-height: 1;
  }
  .company {
    position: absolute; left: 44px; top: 418px;
    font-weight: 700; font-size: 23px; letter-spacing: 0.5px;
    color: var(--ink-dark); white-space: nowrap;
  }
  .person { position: absolute; left: 44px; top: 480px; }
  .person__name {
    font-weight: 700; font-size: 24px; color: var(--accent-green); line-height: 1.1;
  }
  .person__title { font-size: 17px; color: var(--ink-body); margin-top: 1px; }
  .contacts { position: absolute; left: 44px; top: 550px; list-style: none; }
  .contacts li {
    display: flex; align-items: center; gap: 10px;
    font-size: 17px; color: var(--ink-body); height: 24.5px;
  }
  .contacts svg { width: 12px; height: 12px; flex: none; }
  .back-mark {
    position: absolute; left: 262px; top: 482px;
    display: flex; align-items: center; gap: 6px;
  }
  .back-mark__square { width: 11px; height: 11px; background: var(--accent-green); flex: none; }
  .back-mark__name { font-weight: 700; font-size: 16px; color: var(--white); }
</style>
</head>
<body>
<div class="canvas">
  <section class="card card--front">
    <div class="brand">
      <span class="brand__square"></span>
      <span class="brand__name">TALVENOR</span>
    </div>
    <h1 class="company">TALVENOR CAPITAL LLC</h1>
    <div class="person">
      <p class="person__name">Lukas Varenko</p>
      <p class="person__title">Fund Manager</p>
    </div>
    <ul class="contacts">
      <li>
        <svg viewBox="0 0 12 12" aria-hidden="true"><path d="M2 1l2 0 1 3-1.5 1a6 6 0 0 0 3.5 3.5L8 7l3 1 0 2c0 1-1 1.5-2 1.5C5 11 1 7 1 3c0-1 .5-2 1-2z" fill="var(--accent-green)"/></svg>
        +1 555 284 6190
      </li>
      <li>
        <svg viewBox="0 0 12 12" aria-hidden="true"><rect x="1" y="2.5" width="10" height="7" fill="none" stroke="var(--accent-green)" stroke-width="1.3"/><path d="M1 3l5 3.5L11 3" fill="none" stroke="var(--accent-green)" stroke-width="1.3"/></svg>
        lv@FundTalvenor.com
      </li>
      <li>
        <svg viewBox="0 0 12 12" aria-hidden="true"><circle cx="6" cy="6" r="5" fill="none" stroke="var(--accent-green)" stroke-width="1.2"/><ellipse cx="6" cy="6" rx="2.2" ry="5" fill="none" stroke="var(--accent-green)" stroke-width="1"/><path d="M1 6h10M2 3.5h8M2 8.5h8" stroke="var(--accent-green)" stroke-width="0.9"/></svg>
        www.FundTalvenor.com
      </li>
    </ul>
  </section>

  <section class="card card--back" role="img" aria-label="Dark card back with a faint raised brand pattern">
    <div class="back-mark">
      <span class="back-mark__square"></span>
      <span class="back-mark__name">TALVENOR</span>
    </div>
  </section>
</div>
</body>
</html>
```